International service dog training school needs web design

We need to upgrade our website. The website is https://brightmeadow.studio/
We help trainers and service dog programs learn how to train service dogs with the latest and most ethical training methods. We offer online and in-person coaching services. We would like to see designs that are engaging and communicate professionalism, expertise, and care for the dogs and people we work with. Please also keep the colors already in the logo in the design.

```html
<!DOCTYPE html>
<html lang="en">
<head>
<meta charset="utf-8">
<title>Brightmeadow Institute for Assistance Dog Training</title>
<link href="https://fonts.googleapis.com/css2?family=Jost:wght@300;400;500;600&display=swap" rel="stylesheet">
<style>
:root{
  --blue:#1b74b9;
  --teal:#08a39a;
  --ink:#111418;
  --muted:#4a4f55;
  --white:#ffffff;
}
*{box-sizing:border-box;margin:0;padding:0}
html,body{width:1200px;height:3239px;overflow:hidden;background:var(--white)}
body{font-family:"Jost",sans-serif;color:var(--ink);position:relative}
.abs{position:absolute}
.topline{left:0;top:0;width:1200px;height:4px;background:var(--blue)}
.brand{left:111px;top:22px;display:flex;align-items:center;gap:12px}
.brand-dot{width:58px;height:58px;border-radius:50%;background:var(--blue)}
.brand-name{font-weight:500;color:var(--blue);font-size:19px;line-height:1.15;width:250px}
.call{left:758px;top:4px;width:330px;height:46px;border-radius:23px;background:var(--blue);display:flex;align-items:center;color:#fff;font-weight:500;font-size:16px}
.call-icon{width:46px;height:46px;border-radius:50%;background:var(--teal);display:flex;align-items:center;justify-content:center;margin-right:14px}
.nav{left:491px;top:68px;display:flex;gap:28px;font-size:16px;font-weight:500}
.hero{left:0;top:116px;width:1200px;height:720px}
.hero-title{left:109px;top:326px;width:520px;color:#fff;font-weight:600;font-size:45px;line-height:1.15;letter-spacing:.5px}
.btn{display:inline-flex;align-items:center;justify-content:center;width:164px;height:46px;border-radius:23px;background:var(--blue);color:#fff;font-size:14px;font-weight:600;letter-spacing:.3px}
.hero-btn{left:111px;top:493px}
.dots{left:577px;top:731px;display:flex;gap:4px}
.dots span{width:13px;height:13px;border-radius:50%;background:#fff}
.svc-photo{width:480px;height:211px;border-radius:42px}
.photo-group{background:linear-gradient(120deg,#3b3a44 0%,#7fa6c9 45%,#c7d2dc 100%)}
.photo-class{background:linear-gradient(120deg,#d9d3c4 0%,#7a5a44 50%,#d6d0c2 100%)}
.photo-tiles{background:linear-gradient(135deg,#d8d2c8 0%,#efe9df 60%,#c9c2b6 100%)}
.photo-seminar{background:linear-gradient(160deg,#6f6a66 0%,#9b8676 45%,#3f3a3a 100%)}
.photo-airport{background:linear-gradient(150deg,#e3e6e6 0%,#b9bec0 45%,#3b2a24 75%,#9b2b30 100%)}
.svc-title{font-size:44px;font-weight:500;line-height:1.17;width:520px;letter-spacing:.6px}
.svc-text{font-size:13px;line-height:1.75;width:450px;margin-top:10px}
.band{left:0;top:2478px;width:1200px;height:450px}
.book-title{left:111px;top:2625px;color:#fff;font-size:45px;font-weight:500;line-height:1.15}
.book-sub{left:111px;top:2742px;width:420px;color:#fff;font-size:17px;line-height:1.35;font-weight:300}
.btn-white{background:#fff;color:var(--teal)}
.foot-title{left:111px;top:2993px;font-size:35px;font-weight:500;letter-spacing:.5px}
.foot-text{left:111px;top:3044px;width:330px;font-size:15px;color:var(--muted);line-height:1.5;font-weight:300}
.foot-links{left:575px;top:3004px;font-size:15px;line-height:1.5;color:var(--muted);font-weight:300}
.foot-links h4{font-weight:600;color:var(--ink);font-size:15px;margin-bottom:12px}
.social{left:954px;top:3082px;display:flex;gap:7px}
.social span{width:29px;height:29px;border-radius:50%;background:var(--ink)}
.copy{left:111px;top:3184px;font-size:14px}
.legal{left:840px;top:3184px;font-size:14px}
</style>
</head>
<body>
<div class="abs topline"></div>
<div class="abs brand"><span class="brand-dot"></span><span class="brand-name">Helena Marwick Ph.D. Brightmeadow Institute</span></div>
<div class="abs call"><span class="call-icon"><svg width="16" height="16" viewBox="0 0 24 24"><path fill="#fff" d="M6.6 10.8a15.1 15.1 0 0 0 6.6 6.6l2.2-2.2c.3-.3.7-.4 1-.2 1.1.4 2.3.6 3.6.6.6 0 1 .4 1 1V20c0 .6-.4 1-1 1A17 17 0 0 1 3 4c0-.6.4-1 1-1h3.5c.6 0 1 .4 1 1 0 1.3.2 2.5.6 3.6.1.3 0 .7-.2 1z"/></svg></span>Call us Today : +1 555 014 2290</div>
<nav class="abs nav"><span>BIAD</span><span>The Center</span><span>Helping organizations</span><span>Teaching Trainers</span><span>Research Contact</span></nav>

<svg class="abs hero" viewBox="0 0 1200 720" role="img" aria-label="Photo of a trainer holding a golden dog's paw on the grass">
<defs><linearGradient id="hg" x1="0" y1="0" x2="1" y2="1"><stop offset="0" stop-color="#3f7d95"/><stop offset=".6" stop-color="#6d8f5d"/><stop offset="1" stop-color="#8f9f55"/></linearGradient></defs>
<path d="M0 0H1200V616Q900 700 600 688Q260 680 0 614Z" fill="url(#hg)"/>
<path d="M160 654Q520 720 780 690Q1010 665 1200 620V640Q1000 700 760 712Q480 722 160 654Z" fill="var(--teal)"/>
</svg>
<h1 class="abs hero-title">THE BRIGHTMEADOW INSTITUTE FOR ASSISTANCE DOGS</h1>
<a class="abs btn hero-btn">GET STARTED</a>
<div class="abs dots"><span></span><span></span><span></span></div>

<section>
<div class="abs svc-photo photo-group" style="left:111px;top:910px" role="img" aria-label="Group photo of trainers with their dogs"></div>
<div class="abs" style="left:625px;top:898px"><h2 class="svc-title">Organization/Program Consulting</h2><p class="svc-text">Helping organizations get started, improve their training program, and add services</p><a class="btn" style="margin-top:12px">LEARN MORE</a></div>

<div class="abs" style="left:111px;top:1228px"><h2 class="svc-title">Professional coaching /teaching for dog trainers</h2><p class="svc-text">Helping dog trainers improve their skills and learn about service dog training and medical alert dog training.</p><a class="btn" style="margin-top:12px">LEARN MORE</a></div>
<div class="abs svc-photo photo-class" style="left:608px;top:1234px" role="img" aria-label="Trainer working with a dog in a classroom"></div>

<div class="abs svc-photo photo-tiles" style="left:111px;top:1557px" role="img" aria-label="Detection dog sniffing a scent tin"></div>
<div class="abs" style="left:625px;top:1546px"><h2 class="svc-title">Collaborating in Research Projects</h2><p class="svc-text">Collaborating in research studies in the field of Medical Detection Dogs.</p><a class="btn" style="margin-top:34px">LEARN MORE</a></div>

<div class="abs" style="left:111px;top:1872px"><h2 class="svc-title">Presentations and Seminars</h2><p class="svc-text">Sharing knowledge about service dogs and medical detection.</p><a class="btn" style="margin-top:34px">LEARN MORE</a></div>
<div class="abs svc-photo photo-seminar" style="left:608px;top:1881px" role="img" aria-label="Audience at a seminar"></div>

<div class="abs svc-photo photo-airport" style="left:111px;top:2204px" role="img" aria-label="Service dog in a vest watching planes at an airport"></div>
<div class="abs" style="left:625px;top:2194px"><h2 class="svc-title" style="width:330px">International services</h2><p class="svc-text">Fluent in both English and French, in-person and online coaching around the world.</p><a class="btn" style="margin-top:12px">LEARN MORE</a></div>
</section>

<svg class="abs band" viewBox="0 0 1200 450">
<defs>
<radialGradient id="mg" cx=".5" cy=".45" r=".6"><stop offset="0" stop-color="#d6a464" stop-opacity=".85"/><stop offset="1" stop-color="#c08a4b" stop-opacity="0"/></radialGradient>
<linearGradient id="bk" x1="0" y1="0" x2="0" y2="1"><stop offset="0" stop-color="#f4efe8"/><stop offset=".45" stop-color="#e9e2d6"/><stop offset=".7" stop-color="#c9a46d"/><stop offset="1" stop-color="#c8202a"/></linearGradient>
</defs>
<path d="M0 75Q300 30 600 38Q920 40 1200 80V450H0Z" fill="var(--teal)"/>
<path d="M595 38Q920 40 1200 80V300Q900 280 700 180Q610 120 595 38Z" fill="var(--blue)"/>
<rect x="706" y="134" width="171" height="256" fill="url(#bk)" role="img" aria-label="Book cover with a service dog"/>
<ellipse cx="1005" cy="250" rx="170" ry="220" fill="url(#mg)" role="img" aria-label="Cartoon illustration of a happy dog mascot"/>
</svg>
<h2 class="abs book-title">New book from<br>Helena Marwick Ph.D.</h2>
<p class="abs book-sub">Raising a Calm Service Partner: A Field Guide to Public Access Readiness</p>
<a class="abs btn btn-white" style="left:115px;top:2798px">LEARN MORE</a>

<footer>
<h3 class="abs foot-title">STAYING AHEAD</h3>
<p class="abs foot-text">Science-based and ethical training methods for the modern service dog trainer.</p>
<a class="abs btn" style="left:111px;top:3093px">LEARN MORE</a>
<div class="abs foot-links"><h4>Links</h4>BIAD<br>The Center<br>Helping organizations<br>Teaching Trainers<br>Research Contact</div>
<div class="abs brand" style="left:830px;top:2994px"><span class="brand-dot" style="width:48px;height:48px"></span><span class="brand-name" style="font-size:17px;width:200px">Helena Marwick Ph.D. Brightmeadow Institute</span></div>
<div class="abs social"><span aria-label="Social link"></span><span aria-label="Social link"></span><span aria-label="Social link"></span><span aria-label="Social link"></span></div>
<p class="abs copy">Copyright © 2021. All Rights Reserved</p>
<p class="abs legal">Terms and Conditions | Privacy Policy</p>
</footer>
</body>
</html>
```